Automotive Accessories Business Card

Design a business template that match our new logo design and our industry.

https://www.qelmotorgear.com/

Target Market(s)

Aftermarket auto parts and accessories

Industry/Entity Type

automotive

Contact Information for Business Card

company logo

Font styles to use
Serif
Sans Serif

Colors
EB3D1F
EC4F4E
F09395
F8D3D4
FCEDEE

```html
<!DOCTYPE html>
<html lang="en">
<head>
<meta charset="utf-8">
<title>Qelmo Motor Gear – Business Card</title>
<link href="https://fonts.googleapis.com/css2?family=Montserrat:wght@400;500;700&display=swap" rel="stylesheet">
<style>
  :root {
    --bg: #d9d9d7;
    --paper: #ffffff;
    --charcoal: #434345;
    --charcoal-deep: #3a3a3c;
    --ink: #3b3b3d;
    --red: #e41e26;
    --rule: #4a4a4a;
    --emboss: #2f2f31;
  }
  * { box-sizing: border-box; margin: 0; padding: 0; }
  html, body { width: 1200px; height: 801px; overflow: hidden; }
  body {
    background: var(--bg);
    font-family: "Montserrat", sans-serif;
    position: relative;
  }
  .card {
    position: absolute;
    top: 252px;
    width: 520px;
    height: 297px;
    border-bottom: 6px solid var(--red);
    box-shadow: 0 14px 26px rgba(0,0,0,0.22);
  }
  .card--front { left: 50px; background: var(--paper); color: var(--ink); }
  .card--back { left: 630px; background: var(--charcoal); }

  .brand {
    position: absolute;
    top: 34px;
    right: 34px;
    display: flex;
    align-items: center;
    gap: 9px;
    font-weight: 700;
    font-size: 20px;
    letter-spacing: 0.06em;
    color: var(--charcoal-deep);
    text-transform: uppercase;
  }
  .brand__square { width: 14px; height: 14px; background: var(--red); }

  .holder { position: absolute; left: 34px; top: 120px; }
  .holder__name {
    font-weight: 700;
    font-size: 22px;
    letter-spacing: 0.04em;
    color: var(--red);
    text-transform: uppercase;
  }
  .holder__title { font-size: 14px; margin-top: 2px; }

  .divider {
    position: absolute;
    left: 34px;
    right: 34px;
    top: 186px;
    height: 1px;
    background: var(--rule);
  }

  .contact {
    position: absolute;
    left: 34px;
    top: 200px;
    list-style: none;
    font-size: 13px;
    line-height: 22px;
  }
  .contact li { display: flex; align-items: center; gap: 8px; }
  .contact svg { width: 11px; height: 11px; fill: var(--red); flex: none; }

  .address {
    position: absolute;
    right: 34px;
    top: 200px;
    font-size: 13px;
    line-height: 20px;
    text-align: right;
    font-style: normal;
  }

  .brand--large {
    position: absolute;
    inset: 0;
    display: flex;
    align-items: center;
    justify-content: center;
    gap: 14px;
    font-weight: 700;
    font-size: 34px;
    letter-spacing: 0.06em;
    color: var(--emboss);
    text-transform: uppercase;
  }
  .brand--large .brand__square { width: 24px; height: 24px; background: var(--emboss); }
</style>
</head>
<body>
  <section class="card card--front" aria-label="Business card front">
    <div class="brand"><span class="brand__square"></span>Qelmo Motor Gear</div>

    <div class="holder">
      <p class="holder__name">Dorian Vale</p>
      <p class="holder__title">CEO/Founder</p>
    </div>

    <div class="divider"></div>

    <ul class="contact">
      <li>
        <svg viewBox="0 0 24 24" aria-hidden="true"><path d="M6.6 10.8a15.1 15.1 0 0 0 6.6 6.6l2.2-2.2a1 1 0 0 1 1-.25 11.4 11.4 0 0 0 3.6.57 1 1 0 0 1 1 1V20a1 1 0 0 1-1 1A17 17 0 0 1 3 4a1 1 0 0 1 1-1h3.5a1 1 0 0 1 1 1c0 1.25.2 2.45.57 3.57a1 1 0 0 1-.25 1z"/></svg>
        1-866-555-0142
      </li>
      <li>
        <svg viewBox="0 0 24 24" aria-hidden="true"><path d="M2 5h20v14H2z M2 5l10 8 10-8" /></svg>
        sales@qelmotorgear.com
      </li>
      <li>
        <svg viewBox="0 0 24 24" aria-hidden="true"><circle cx="12" cy="12" r="10"/></svg>
        www.qelmotorgear.com
      </li>
    </ul>

    <address class="address">
      248 W. Harbor Ave. Suite B<br>
      Fontana, CA, 92335
    </address>
  </section>

  <section class="card card--back" aria-label="Business card back">
    <div class="brand brand--large"><span class="brand__square"></span>Qelmo Motor Gear</div>
  </section>
</body>
</html>
```